Stationery Design Project for Nimbora, Chicago

Nimbora, a street parking application which helps car drivers find a street parking spot by offering an ideal path along which to look for parking. This path is calculated by our algorithm based on data (e.g. historical data, baseball games schedule, etc.). Along this path the driver will find a spot and will also save 70% of the search time. Customer we target is reg. between 21 and 45 yo.

We envision something young, fresh, bright and original. Slightly abstract maybe. It should represent the idea and elements of finding street parking in the city, e.g. car(s), parking spot, people, city, etc. (just ideas!).

Logo is attached.

Requirement:
- Business Cards (2 Sided Full Color CMYK)
- Letterhead (1 Sided Full Color CMYK)
- Envelope (1 Sided Full Color CMYK)
- Sticker (1 Sided Full Color CMYK), round with a 2inch diameter.

Reason: We're starting to get more and more designs and need more time to look into all of them. Very exciting!! Thanks to everybody!

Hi all, we're in the process of selecting our favs. Though choices!!! Really good submissions. Will keep you posted and sorry for the delay.

Target Market(s)

Car drivers and owners between 21 and 45

Industry/Entity Type

Parking

Requirements
Must have
• Sticker should be round and include company URL nimbora.com and the new logo which we will attach soon.
Should not have
• Should not be too serious or boring.

```html
<!DOCTYPE html>
<html lang="en">
<head>
<meta charset="utf-8">
<title>Nimbora Business Card</title>
<link href="https://fonts.googleapis.com/css2?family=Open+Sans:wght@400;600;700&display=swap" rel="stylesheet">
<style>
  :root {
    --backdrop: #e4e4e4;
    --card: #ffffff;
    --ink: #1a1a1a;
    --ink-soft: #5e5e5e;
    --ink-body: #2b2b2b;
    --brand-blue: #1f4fc4;
    --wash-strong: #dfe7f4;
    --wash-light: #f3f6fb;
    --rule: #444444;
  }
  * { margin: 0; padding: 0; box-sizing: border-box; }
  html, body { width: 954px; height: 1200px; overflow: hidden; }
  body {
    background: var(--backdrop);
    font-family: "Open Sans", Arial, sans-serif;
    color: var(--ink-body);
    position: relative;
  }
  .card {
    position: absolute;
    left: 75px;
    width: 797px;
    height: 455px;
    background: var(--card);
    border-radius: 28px;
    box-shadow: 0 4px 10px rgba(0,0,0,0.18);
    overflow: hidden;
  }
  .card--front { top: 113px; }
  .card--back { top: 660px; }

  .brand { position: absolute; display: flex; align-items: center; z-index: 1; }
  .brand__dot {
    width: 157px; height: 157px; border-radius: 50%;
    background: var(--brand-blue);
    flex: none;
  }
  .brand__name {
    font-weight: 400;
    font-size: 100px;
    line-height: 1;
    color: var(--ink);
    margin-left: 29px;
    margin-top: -14px;
  }
  .card--front .brand { left: 105px; top: 51px; }
  .card--back .brand { left: 76px; top: 88px; }
  .card--back .brand__name { font-size: 106px; }

  .backdrop-mark {
    position: absolute;
    left: 221px; top: 0;
    width: 380px; height: 455px;
    background: radial-gradient(ellipse at 50% 50%, var(--wash-strong) 0%, var(--wash-light) 55%, rgba(255,255,255,0) 75%);
    z-index: 0;
  }

  .holder {
    position: absolute; top: 262px; left: 0; width: 100%;
    text-align: center; color: var(--ink-soft);
  }
  .holder__name { font-size: 24px; font-weight: 600; }
  .holder__role { font-size: 19px; font-weight: 600; }
  .holder__bar { font-size: 22px; padding: 0 6px; }

  .contact {
    position: absolute; top: 328px; left: 0; width: 100%;
    display: flex; justify-content: center;
    font-size: 19px; line-height: 28px;
  }
  .contact__phones { text-align: right; padding-right: 12px; }
  .contact__address { border-left: 1.5px solid var(--rule); padding-left: 10px; }
  .contact b { font-weight: 700; color: var(--ink); }

  .online {
    position: absolute; top: 408px; left: 0; width: 100%;
    text-align: center; font-size: 19px;
  }
  .online__bar { padding: 0 8px; }

  .url {
    position: absolute; top: 392px; left: 0; width: 100%;
    text-align: center; font-size: 32px; color: var(--ink);
    z-index: 1;
  }
</style>
</head>
<body>
  <section class="card card--front">
    <div class="brand">
      <div class="brand__dot"></div>
      <span class="brand__name">nimbora</span>
    </div>
    <p class="holder">
      <span class="holder__name">Your Name</span><span class="holder__bar">|</span><span class="holder__role">Designation</span>
    </p>
    <div class="contact">
      <div class="contact__phones">
        <div><b>t</b> : 123-456-7890</div>
        <div><b>m</b> : 123-456-7890</div>
      </div>
      <div class="contact__address">
        <div>City Name, Street Name</div>
        <div>State Name, Country Code</div>
      </div>
    </div>
    <p class="online">
      <b>e</b> : name@nimbora.com<span class="online__bar">|</span><b>w</b> : www.nimbora.com
    </p>
  </section>

  <section class="card card--back">
    <div class="backdrop-mark" role="img" aria-label="Faint pale blue brand decoration behind the logo"></div>
    <div class="brand">
      <div class="brand__dot"></div>
      <span class="brand__name">nimbora</span>
    </div>
    <p class="url">www.nimbora.com</p>
  </section>
</body>
</html>
```